New Innovative Counselling and psychotherapy Service needs Business Card design

Keep it simple and professional. On one side, just company name and logo (perhaps in all blue) and maybe a tag line.

On other side (all white) my name and Qualifications in centre

Industry/Entity Type

Health And Wellness

Contact Information for Business Card

Dara Whelby
Counsellor & Psychotherapist
BSc (Psychol.), BA, Dip. (Couns. & Psych.), PG.Cert (CBT), FGTrK, ONRE

I will also require Mobile no, Email and web site address of which I'll pass on to final designer.

Font styles to use
Sans Serif

Requirements
Must have
• My Logo Only and please use the colours in logo that is in it.
Should not have
• Any other images

```html
<!DOCTYPE html>
<html lang="en">
<head>
<meta charset="utf-8">
<title>Thrive Lane – Business Card</title>
<link rel="stylesheet" href="https://fonts.googleapis.com/css2?family=Montserrat:wght@400;500&family=Roboto:wght@400;700&display=swap">
<style>
  :root {
    --stage: #3a3a3a;
    --card: #1e1f21;
    --card-edge: #2a2b2d;
    --blue: #3cafe8;
    --green: #7cc242;
    --white: #ffffff;
    --muted: #4a4b4e;
  }
  * { box-sizing: border-box; margin: 0; padding: 0; }
  html, body { width: 799px; height: 1200px; overflow: hidden; }
  body {
    background: var(--stage);
    font-family: "Roboto", Arial, sans-serif;
    position: relative;
  }
  .card {
    position: absolute;
    left: 90px;
    width: 620px;
    height: 354px;
    border-radius: 22px;
    background: var(--card);
    border: 1px solid var(--card-edge);
    overflow: hidden;
  }
  .card--front { top: 130px; }
  .card--back { top: 716px; }

  /* Front */
  .front-mark {
    position: absolute;
    inset: 0;
    display: flex;
    align-items: center;
    justify-content: center;
    gap: 18px;
  }
  .front-mark__dot {
    width: 54px; height: 54px;
    border-radius: 50%;
    background: var(--muted);
  }
  .front-mark__name {
    font-family: "Montserrat", Arial, sans-serif;
    font-weight: 500;
    font-size: 40px;
    color: var(--muted);
  }

  /* Back */
  .brand {
    position: absolute;
    top: 34px; left: 34px;
    display: flex;
    align-items: center;
    gap: 22px;
  }
  .brand__dot {
    width: 70px; height: 70px;
    border-radius: 50%;
    background: var(--blue);
  }
  .brand__name {
    font-family: "Montserrat", Arial, sans-serif;
    font-weight: 400;
    font-size: 48px;
    color: var(--white);
    letter-spacing: 0.5px;
  }
  .person {
    position: absolute;
    top: 150px; left: 34px;
    color: var(--white);
  }
  .person__name {
    font-weight: 700;
    font-size: 24px;
    color: var(--blue);
    margin-bottom: 6px;
  }
  .person__role, .person__quals {
    font-size: 13px;
    line-height: 1.35;
  }
  .contact {
    position: absolute;
    top: 198px; left: 340px;
    list-style: none;
    color: var(--white);
    font-size: 15px;
    line-height: 1.45;
  }
  .contact li { display: flex; align-items: center; gap: 10px; }
  .contact svg { width: 14px; height: 14px; flex: none; }
  .bands {
    position: absolute;
    left: 0; bottom: 0;
    width: 620px; height: 80px;
  }
  .tagline {
    position: absolute;
    left: 340px; bottom: 26px;
    font-size: 17px;
    color: var(--white);
  }
</style>
</head>
<body>

<section class="card card--front" aria-label="Card front">
  <div class="front-mark">
    <span class="front-mark__dot"></span>
    <span class="front-mark__name">Thrive Lane</span>
  </div>
</section>

<section class="card card--back" aria-label="Card back">
  <div class="brand">
    <span class="brand__dot"></span>
    <span class="brand__name">Thrive Lane</span>
  </div>

  <div class="person">
    <p class="person__name">Dara Whelby</p>
    <p class="person__role">Counsellor &amp; Psychotherapist</p>
    <p class="person__quals">BSc (Psychol.), BA, Dip. (Couns. &amp;<br>Psych.), PG.Cert (CBT), FGTrK, ONRE</p>
  </div>

  <ul class="contact">
    <li>
      <svg viewBox="0 0 16 16" aria-hidden="true"><path fill="#3cafe8" d="M3 2h3l1 4-2 1c1 2 2 3 4 4l1-2 4 1v3c0 1-1 1-1 1C7 14 2 9 2 3c0 0 0-1 1-1z"/></svg>
      0161 555 0148
    </li>
    <li>
      <svg viewBox="0 0 16 16" aria-hidden="true"><rect x="1" y="3" width="14" height="10" fill="#7cc242"/><path d="M1 3l7 6 7-6" fill="none" stroke="#1e1f21" stroke-width="1.3"/></svg>
      dara.w@ThriveLane.com
    </li>
    <li>
      <svg viewBox="0 0 16 16" aria-hidden="true"><circle cx="8" cy="8" r="7" fill="#3cafe8"/><path d="M1 8h14M8 1c-3 4-3 10 0 14M8 1c3 4 3 10 0 14" fill="none" stroke="#1e1f21" stroke-width="1"/></svg>
      www.ThriveLane.com
    </li>
  </ul>

  <svg class="bands" viewBox="0 0 620 80" aria-hidden="true">
    <rect x="0" y="14" width="290" height="8" fill="var(--green)"/>
    <path d="M270 22 Q300 22 315 10 Q328 0 350 0 L620 0 L620 80 L270 80 Z" fill="var(--blue)"/>
  </svg>
  <p class="tagline">A tag line goes here</p>
</section>

</body>
</html>
```